Website design for Silver Harbor Trading Inc

We are looking to build a website for our company. We are a scrap metal recycling company based out of Los Angeles. We purchase scrap metal in the US and ship them to China for recycling into fresh metal ores to supply industrial users. We would designs that emphasize the color green given our name and the nature of our business. Recycling themes are welcomed. We already have a URL at:
http://silverharbortradinginc.example/
At this point, I would like 4 pages:
- Home page
- About Us
- Resources
- Contact us
Our sister company is Maple Crest Intl Inc and they have a website that we can use as a starting point.
http://www.maplecrest-intl.example/
Our competitor has a website below. However we dislike the design given we believe it looks rather dull.
http://www.orientalloysalvage.example/en/
Lastly, this is for a website shell only. Please design the template, graphics, and color schemes. We will write the contents later.

```html
<!DOCTYPE html>
<html lang="en">
<head>
<meta charset="utf-8">
<title>Silver Harbor Trading Inc — Scrap Metal Recycling</title>
<link href="https://fonts.googleapis.com/css2?family=Nunito+Sans:wght@400;600;700&family=Arimo:wght@400;700&display=swap" rel="stylesheet">
<style>
:root{
  --green:#2f6d12;
  --green-dark:#245a0c;
  --green-light:#4a8a1e;
  --nav-divider:#5c9530;
  --ink:#111;
  --text:#3a3a3a;
  --muted:#888;
  --panel:#efefef;
  --page-top:#f4f4f4;
  --page-fade:#e4e5e4;
  --white:#fff;
  --footer-top:#6a6a6a;
  --footer-bottom:#2b2b2b;
}
*{margin:0;padding:0;box-sizing:border-box}
html,body{width:1200px;height:961px;overflow:hidden}
body{position:relative;background:var(--white);font-family:"Nunito Sans",sans-serif;color:var(--text)}
.page-backdrop{position:absolute;left:0;top:0;width:1200px;height:369px;background:linear-gradient(var(--page-top),var(--page-fade));border-bottom:1px solid #d6d6d6}
.sheet{position:absolute;left:146px;top:114px;width:904px;height:811px;background:var(--white);box-shadow:0 0 4px rgba(0,0,0,.18)}

.brand{position:absolute;left:153px;top:24px;display:flex;align-items:center;gap:9px}
.brand-dot{width:25px;height:25px;border-radius:50%;background:var(--green)}
.brand-name{font-size:24px;font-weight:600;color:var(--green);letter-spacing:-.3px}

.search{position:absolute;left:873px;top:23px;width:166px;height:25px;background:var(--white);border:1px solid #d4d4d4}
.search svg{position:absolute;right:6px;top:5px}

.main-nav{position:absolute;left:146px;top:70px;width:904px;height:44px;background:linear-gradient(var(--green-light),var(--green-dark));display:flex;border-radius:3px 3px 0 0}
.main-nav a{display:flex;align-items:center;justify-content:center;color:var(--white);text-decoration:none;font-size:12px;font-weight:600;word-spacing:6px;border-right:1px solid var(--nav-divider)}
.main-nav a:last-child{border-right:none}

.hero{position:absolute;left:146px;top:114px;width:904px;height:281px;background:linear-gradient(160deg,#8c887c 0%,#5e5a4f 35%,#9a8b62 55%,#4b463c 80%,#3a3732 100%)}
.hero-caption{position:absolute;left:0;bottom:0;width:100%;height:66px;background:rgba(40,40,40,.72);display:flex;align-items:center;padding-left:41px;color:var(--white);font-size:16.5px;font-weight:600}

.intro{position:absolute;left:168px;top:416px;width:860px}
.intro h1{font-size:22px;font-weight:400;color:var(--ink);letter-spacing:-.3px;margin-bottom:16px}
.intro p{font-size:10.5px;line-height:13.7px;color:#444;margin-bottom:12px;padding-left:2px}

.services{position:absolute;left:169px;top:574px;width:860px}
.service{position:absolute;width:194px}
.service .thumb{width:194px;height:94px;border-radius:4px}
.service h3{font-size:13px;font-weight:700;color:var(--green);margin-top:14px}
.service .more{display:block;font-family:Arimo,sans-serif;font-size:11px;font-weight:700;color:#666;margin-top:6px;text-decoration:none}

.bottom-panel{position:absolute;left:146px;top:746px;width:904px;height:179px;background:var(--panel)}
.section-title{position:absolute;font-size:18.5px;font-weight:400;color:#555;letter-spacing:-.4px}
.process{position:absolute;left:169px;top:811px;display:flex}
.step{position:relative;width:63px;margin-right:24px;text-align:center}
.step:last-child{margin-right:0}
.step .thumb{width:63px;height:69px;border-radius:3px}
.step span{display:block;font-family:Arimo,sans-serif;font-size:11.5px;font-weight:700;color:#555;margin-top:14px;white-space:nowrap;margin-left:-15px;margin-right:-15px}
.step .chev{position:absolute;right:-17px;top:26px}

.news{position:absolute;left:714px;top:780px;width:302px}
.news .view-all{position:absolute;right:0;top:15px;font-family:Arimo,sans-serif;font-size:9.5px;color:#777;text-decoration:underline}
.news-item{font-family:Arimo,sans-serif;font-size:10px;line-height:12px;color:#222}
.news-item time{display:block;color:#8a8a8a;margin-top:6px}

.site-footer{position:absolute;left:0;top:925px;width:1200px;height:36px;background:linear-gradient(var(--footer-top),var(--footer-bottom));font-family:Arimo,sans-serif;font-size:10.5px;color:#ddd}
.site-footer nav{position:absolute;left:156px;top:12px;display:flex;gap:14px}
.site-footer nav a{color:#ddd;text-decoration:none}
.site-footer small{position:absolute;right:157px;top:12px;font-size:10.5px}
</style>
</head>
<body>
<div class="page-backdrop"></div>
<div class="sheet"></div>

<header>
  <div class="brand"><span class="brand-dot"></span><span class="brand-name">Silver Harbor Trading Inc</span></div>
  <div class="search">
    <svg width="14" height="14" viewBox="0 0 14 14"><circle cx="5.5" cy="5.5" r="4.3" fill="none" stroke="#bbb" stroke-width="1.8"/><line x1="8.6" y1="8.6" x2="13" y2="13" stroke="#bbb" stroke-width="2"/></svg>
  </div>
</header>

<nav class="main-nav">
  <a href="#" style="width:101px">HOME</a>
  <a href="#" style="width:126px">ABOUT US</a>
  <a href="#" style="width:152px">OUR COMPANY</a>
  <a href="#" style="width:170px">SCRAP RECYCLING</a>
  <a href="#" style="width:126px">INVESTORS</a>
  <a href="#" style="width:110px">CAREERS</a>
  <a href="#" style="width:119px">CONTACT</a>
</nav>

<section class="hero" role="img" aria-label="Close-up photo of a pile of scrap metal pipe fittings and nuts">
  <div class="hero-caption">This is Draftline's version &nbsp;of Lorem Ipsum Proin gravida nibh vel velit</div>
</section>

<section class="intro">
  <h1>Scrap Metal Recycling</h1>
  <p>This is Draftline's version &nbsp;of Lorem Ipsum. Proin gravida nibh vel velit auctor aliquet. Aenean sollicitudin, lorem quis bibendum auctor, nisi elit consequat ipsum, nec sagittis sem nibh id elit. Duis sed odio sit amet nibh vulputate cursus a sit amet mauris.</p>
  <p>Morbi accumsan ipsum velit. Nam nec tellus a odio tincidunt auctor a ornare odio. Sed non &nbsp;mauris vitae erat consequat auctor eu in elit. Class aptent taciti sociosqu ad litora torquent per conubia nostra, per inceptos himenaeos. Mauris in erat justo. Nullam ac urna eu felis dapibus condimentum sit amet a augue. Sed non neque elit. &nbsp;This is Draftline's version &nbsp;of Lorem Ipsum. Proin gravida nibh vel velit auctor alique</p>
</section>

<section class="services">
  <article class="service" style="left:0;top:0">
    <div class="thumb" role="img" aria-label="Photo of shredded silver ferrous scrap" style="background:linear-gradient(135deg,#c9ccce,#7d8286 50%,#b7babc)"></div>
    <h3 style="margin-top:12px">Ferrous Metal Process</h3>
    <a class="more" href="#" style="margin-top:4px;padding-left:2px">more »</a>
  </article>
  <article class="service" style="left:221px;top:0">
    <div class="thumb" role="img" aria-label="Photo of rusty non-ferrous scrap pile" style="background:linear-gradient(135deg,#8a4f2c,#4a2c1e 50%,#a36a3e)"></div>
    <h3 style="margin-top:17px;margin-left:-1px">Recycled Non-Ferrous metal</h3>
    <a class="more" href="#">more »</a>
  </article>
  <article class="service" style="left:442px;top:0">
    <div class="thumb" role="img" aria-label="Photo of a crane grapple over a scrap heap" style="background:linear-gradient(#7f9cc4,#aab9cf 45%,#6d6457 70%,#4f463b)"></div>
    <h3 style="margin-top:17px">Shredding</h3>
    <a class="more" href="#">more »</a>
  </article>
  <article class="service" style="left:665px;top:0">
    <div class="thumb" role="img" aria-label="Photo of a worker sorting metal scrap in a yard" style="background:linear-gradient(135deg,#5b5148,#8e8273 50%,#3f3a35)"></div>
    <h3 style="margin-top:17px">Metal Sheets</h3>
    <a class="more" href="#">more »</a>
  </article>
</section>

<section class="bottom-panel"></section>
<h2 class="section-title" style="left:167px;top:767px">Our Recycling Process</h2>
<div class="process">
  <div class="step"><div class="thumb" role="img" aria-label="Photo of an excavator feeding scrap" style="background:linear-gradient(#c9b3a5,#7b5e4c)"></div><span>Feeding</span><svg class="chev" width="8" height="16" viewBox="0 0 8 16"><polyline points="1,1 7,8 1,15" fill="none" stroke="#999" stroke-width="1.2"/></svg></div>
  <div class="step"><div class="thumb" role="img" aria-label="Photo of a compression machine" style="background:linear-gradient(#8a5d5a,#3e3340)"></div><span>Compression</span><svg class="chev" width="8" height="16" viewBox="0 0 8 16"><polyline points="1,1 7,8 1,15" fill="none" stroke="#999" stroke-width="1.2"/></svg></div>
  <div class="step"><div class="thumb" role="img" aria-label="Photo of a green shredding machine" style="background:linear-gradient(#5f8f6a,#2f5a3a)"></div><span>Shredding</span><svg class="chev" width="8" height="16" viewBox="0 0 8 16"><polyline points="1,1 7,8 1,15" fill="none" stroke="#999" stroke-width="1.2"/></svg></div>
  <div class="step"><div class="thumb" role="img" aria-label="Photo of a dust removal tower" style="background:linear-gradient(#b8c7c0,#5f7a6e)"></div><span>Dust Removal</span><svg class="chev" width="8" height="16" viewBox="0 0 8 16"><polyline points="1,1 7,8 1,15" fill="none" stroke="#999" stroke-width="1.2"/></svg></div>
  <div class="step"><div class="thumb" role="img" aria-label="Photo of a separating drum" style="background:linear-gradient(#6e6f7a,#b59a44 55%,#33364a)"></div><span>Seperating</span><svg class="chev" width="8" height="16" viewBox="0 0 8 16"><polyline points="1,1 7,8 1,15" fill="none" stroke="#999" stroke-width="1.2"/></svg></div>
  <div class="step"><div class="thumb" role="img" aria-label="Photo of processed metal output pile" style="background:linear-gradient(#7a5a44,#3b3430)"></div><span>Output</span></div>
</div>

<section class="news">
  <h2 class="section-title" style="position:static">News &amp; Updates</h2>
  <a class="view-all" href="#">view all</a>
  <div class="news-item" style="margin-top:15px">Mauris at blandit nibh. Nam cursus, nunc at hendrerit lobortis<time>Aug 22nd, 2013</time></div>
  <div class="news-item" style="margin-top:17px">Aliquam dictum dapibus lacinia. Quisque quis ipsum pretium, laoreet libero semper, ultricies purus.<time>Aug 18th, 2013</time></div>
</section>

<footer class="site-footer">
  <nav><a href="#">Home</a><a href="#">About Us</a><a href="#">Our Company</a><a href="#">Scrap Recycling</a><a href="#">Investors</a><a href="#">Careers</a><a href="#">Contact</a></nav>
  <small>© 2013 &nbsp;Silver Harbor Trading Inc | &nbsp;All Rights Reserved</small>
</footer>
</body>
</html>
```